Tiskoro

We need a business card for our company is a holding for different business all are different we try to have some air of relax and fun in our projects we add pictures of the office to give you an idea od the mood of the business

Business

```html
<!DOCTYPE html>
<html lang="en">
<head>
<meta charset="utf-8">
<title>Tiskoro – Business Card</title>
<link href="https://fonts.googleapis.com/css2?family=Architects+Daughter&display=swap" rel="stylesheet">
<style>
  :root {
    --stage: #2b2b2b;
    --paper: #ffffff;
    --banana: #f6ef35;
    --cocoa: #5a3614;
    --hand: "Architects Daughter", "Comic Sans MS", cursive;
  }
  * { margin: 0; padding: 0; box-sizing: border-box; }
  html, body {
    width: 1200px;
    height: 1000px;
    overflow: hidden;
    background: var(--stage);
  }
  .stage {
    position: relative;
    width: 1200px;
    height: 1000px;
  }

  .card-slot { position: absolute; }
  .card-slot--portrait {
    left: 50px;
    top: 160px;
    width: 380px;
    height: 680px;
  }
  .card-slot--landscape {
    left: 480px;
    top: 310px;
    width: 680px;
    height: 380px;
  }

  .card {
    position: absolute;
    width: 680px;
    height: 380px;
    background: var(--paper);
    overflow: hidden;
    font-family: var(--hand);
    font-variant: small-caps;
    color: var(--cocoa);
    box-shadow: 0 6px 18px rgba(0,0,0,.45);
  }
  .card--rotated {
    left: 50%;
    top: 50%;
    transform: translate(-50%, -50%) rotate(-90deg);
  }
  .card__shapes {
    position: absolute;
    inset: 0;
    width: 100%;
    height: 100%;
  }
  .card__shapes .fill-banana { fill: var(--banana); }
  .card__shapes .fill-paper { fill: var(--paper); }

  .card__brand {
    position: absolute;
    left: 318px;
    top: 28px;
    width: 350px;
    font-family: var(--hand);
    font-variant: normal;
    font-size: 112px;
    line-height: 0.86;
    color: var(--cocoa);
  }
  .card__brand-line { display: block; }

  .card__name {
    position: absolute;
    left: 30px;
    top: 34px;
    font-size: 34px;
    font-weight: 400;
    letter-spacing: 2px;
    color: var(--banana);
    text-shadow: 2px 2px 0 var(--cocoa);
  }
  .card__position {
    position: absolute;
    left: 200px;
    top: 82px;
    font-size: 18px;
    letter-spacing: 1px;
  }
  .card__contact {
    position: absolute;
    left: 28px;
    top: 196px;
    list-style: none;
    letter-spacing: 1.5px;
  }
  .card__contact li { line-height: 1.9; }
  .card__phone { font-size: 23px; padding-left: 8px; }
  .card__email { font-size: 18px; }
</style>
</head>
<body>
<main class="stage">

  <div class="card-slot card-slot--portrait">
    <article class="card card--rotated">
      <svg class="card__shapes" viewBox="0 0 680 380" aria-hidden="true">
        <rect class="fill-banana" x="285" y="0" width="395" height="380"/>
        <path class="fill-paper" d="M285,232 C300,322 470,345 560,312 C620,290 660,240 680,195 L680,300 C650,350 610,372 560,380 L360,380 C320,360 295,330 285,300 Z"/>
      </svg>
      <div class="card__brand"><span class="card__brand-line">Tis</span><span class="card__brand-line">koro</span></div>
      <h1 class="card__name">Name Surname</h1>
      <p class="card__position">Position</p>
      <ul class="card__contact">
        <li class="card__phone">Phone: 041 56 738</li>
        <li class="card__email">email: tiskoro@tkrmail.com</li>
      </ul>
    </article>
  </div>

  <div class="card-slot card-slot--landscape">
    <article class="card">
      <svg class="card__shapes" viewBox="0 0 680 380" aria-hidden="true">
        <rect class="fill-banana" x="285" y="0" width="395" height="380"/>
        <path class="fill-paper" d="M285,232 C300,322 470,345 560,312 C620,290 660,240 680,195 L680,300 C650,350 610,372 560,380 L360,380 C320,360 295,330 285,300 Z"/>
      </svg>
      <div class="card__brand"><span class="card__brand-line">Tis</span><span class="card__brand-line">koro</span></div>
      <h2 class="card__name">Name Surname</h2>
      <p class="card__position">Position</p>
      <ul class="card__contact">
        <li class="card__phone">Phone: 041 56 738</li>
        <li class="card__email">email: tiskoro@tkrmail.com</li>
      </ul>
    </article>
  </div>

</main>
</body>
</html>
```